Web design for Crowdfunding site HopeWingsRally.com

We need a web design for christian crowdfunding website. Here is the challenge: We need responsive layout that is targeted first in iPad size of screen. It should also scale somehow down to iPhone size of screens. Web layout can be about the same size as iPad screen.

Screens should work so that main page scrolls not but only certain part of the screen scrolls and always one "page" at time. We can implement these "scrolls" then later with javascript but now we need only design. The challenge is to create this kind of hybrid website / app look.

Target is at first to raise funds to orphan people needing about $40 per month for their living and education. There is always some organization which takes care of these kids. Later there will be other christian missions included. At first we are looking to find monthly supporters.

You can be as creative as you want :) As you see from the look and feel sector, I am not looking any same traditional look which many "help kids" sites have. I am looking to reach now younger generation and therefore iPad and mobile are the main screen sizes.

Inspirational designs:
- https://example-gallery.test/profiles/studiofernlake/designs/482716?from=%2Fbrowse%2Fxhr%2Fdesigns%3Fcategory%3Dmobile-app-design
- http://www.artpoolhub.test/design/8261047 Clear, simple visuals
- http://www.artpoolhub.test/design/7394215 Header
- http://www.artpoolhub.test/design/6048392 Contrast in the colors, i think is powerfull

Some terms could be: Kids play, kids are learning (in the school). No static posture but living like kids are. I wonder also how we could also add little bit gaming style even though the question is of reali life of real people. Giving should be rewarding.

Target Market(s)

People who want help other people.

Industry/Entity Type

Christian

Number of Pages Required

4 page

Requirements
Must have
• Homepage. Mission page (In my wireframes it was one kid).
Nice to have
• Other pages and some idea how to scroll. 4 pages is no must. If you feel easy, please give first some draft and I give comments on that.

```html
<!DOCTYPE html>
<html lang="en">
<head>
<meta charset="utf-8">
<title>HopeWingsRally – Home</title>
<link rel="stylesheet" href="https://fonts.googleapis.com/css2?family=Open+Sans:wght@400;600;700;800&display=swap">
<style>
  :root {
    --page-bg: #ffffff;
    --screen-bg: #040f18;
    --map-tone: #12384d;
    --map-tone-soft: #0b2636;
    --avatar-green: rgba(46, 92, 68, 0.55);
    --avatar-red: rgba(120, 52, 52, 0.55);
    --avatar-teal: rgba(14, 90, 110, 0.6);
    --avatar-sand: rgba(120, 96, 80, 0.5);
    --text-white: #ffffff;
    --text-muted: #b3b8bd;
    --text-footer: #8b9197;
    --icon-tone: #c3c7ca;
    --accent: #fdb813;
    --rule: #4a5258;
    --button-border: #c9ccce;
  }
  * { margin: 0; padding: 0; box-sizing: border-box; }
  html, body {
    width: 1200px; height: 911px; overflow: hidden;
    background: var(--page-bg);
    font-family: "Open Sans", Arial, sans-serif;
  }
  .screen {
    position: absolute; left: 47px; top: 43px;
    width: 1086px; height: 816px;
    background: var(--screen-bg);
    border-radius: 4px; overflow: hidden;
  }
  .hero-art {
    position: absolute; left: 0; top: 130px; width: 1086px; height: 600px;
    background:
      radial-gradient(circle 70px at 200px 210px, var(--avatar-green) 0%, transparent 100%),
      radial-gradient(circle 65px at 705px 110px, var(--avatar-green) 0%, transparent 100%),
      radial-gradient(circle 45px at 353px 127px, var(--avatar-red) 0%, transparent 100%),
      radial-gradient(circle 65px at 868px 360px, var(--avatar-red) 0%, transparent 100%),
      radial-gradient(circle 45px at 601px 232px, var(--avatar-teal) 0%, transparent 100%),
      radial-gradient(circle 75px at 318px 490px, var(--avatar-sand) 0%, transparent 100%),
      radial-gradient(circle 60px at 485px 368px, var(--avatar-sand) 0%, transparent 100%),
      radial-gradient(circle 55px at 730px 484px, rgba(110, 118, 110, 0.45) 0%, transparent 100%),
      radial-gradient(circle 45px at 916px 183px, var(--avatar-green) 0%, transparent 100%),
      radial-gradient(ellipse 28% 38% at 22% 30%, var(--map-tone) 0%, transparent 100%),
      radial-gradient(ellipse 26% 30% at 30% 78%, var(--map-tone-soft) 0%, transparent 100%),
      radial-gradient(ellipse 38% 36% at 70% 28%, var(--map-tone) 0%, transparent 100%),
      radial-gradient(ellipse 16% 30% at 55% 65%, var(--map-tone) 0%, transparent 100%),
      radial-gradient(ellipse 14% 16% at 85% 78%, var(--map-tone) 0%, transparent 100%);
  }
  .hero-shade {
    position: absolute; left: 0; top: 130px; width: 1086px; height: 600px;
    background: rgba(4, 15, 24, 0.25);
  }
  .topbar { position: absolute; left: 0; top: 0; width: 100%; height: 80px; }
  .menu-toggle {
    position: absolute; left: 27px; top: 31px;
    display: flex; align-items: center; gap: 24px;
    color: var(--text-muted); font-size: 14px; font-weight: 700; letter-spacing: 0.3px;
    text-decoration: none;
  }
  .search-icon { position: absolute; left: 257px; top: 31px; }
  .brand {
    position: absolute; left: 0; right: 0; top: 15px; text-align: center;
    color: var(--text-white); font-size: 38px; font-weight: 800; letter-spacing: 0.5px;
  }
  .btn {
    position: absolute; top: 21px; height: 37px; border-radius: 19px;
    font-size: 14px; font-weight: 700; letter-spacing: 0.5px;
    display: flex; align-items: center; justify-content: center; text-decoration: none;
  }
  .btn-login { left: 809px; width: 121px; color: var(--text-white); border: 2px solid var(--button-border); }
  .btn-signup { left: 939px; width: 121px; color: var(--text-white); background: var(--accent); }
  .hero-quote {
    position: absolute; left: 0; right: 0; top: 352px; text-align: center;
    color: var(--text-white); font-size: 33px; font-weight: 700; line-height: 42px;
    letter-spacing: 0.8px;
  }
  .footer { position: absolute; left: 26px; right: 26px; top: 732px; border-top: 1px solid var(--rule); }
  .copyright { position: absolute; left: 0; top: 29px; color: var(--text-footer); font-size: 13px; }
  .social { position: absolute; right: 0; top: 33px; display: flex; gap: 22px; list-style: none; }
  .social li { width: 18px; height: 18px; border-radius: 3px; background: var(--icon-tone); }
</style>
</head>
<body>
  <main class="screen">
    <div class="hero-art" role="img" aria-label="Dark world map with round avatars of diverse people connected by dashed lines"></div>
    <div class="hero-shade"></div>

    <header class="topbar">
      <a class="menu-toggle" href="#">
        <svg width="16" height="14" viewBox="0 0 16 14" aria-hidden="true">
          <rect x="0" y="0" width="16" height="3" fill="#b3b8bd"/>
          <rect x="0" y="5.5" width="16" height="3" fill="#b3b8bd"/>
          <rect x="0" y="11" width="16" height="3" fill="#b3b8bd"/>
        </svg>
        SEE THE MISSION
      </a>
      <svg class="search-icon" width="18" height="18" viewBox="0 0 18 18" aria-label="Search">
        <circle cx="7.5" cy="7.5" r="5.5" fill="none" stroke="#b3b8bd" stroke-width="2.4"/>
        <line x1="11.5" y1="11.5" x2="16.5" y2="16.5" stroke="#b3b8bd" stroke-width="2.8" stroke-linecap="round"/>
      </svg>
      <div class="brand">HopeWingsRally</div>
      <a class="btn btn-login" href="#">LOG IN</a>
      <a class="btn btn-signup" href="#">SIGN UP</a>
    </header>

    <p class="hero-quote">
      “She has a name. She has dreams. She hopes she<br>
      would have a future. He is like you.”<br>
      “1 USD a month will help her and him”
    </p>

    <footer class="footer">
      <p class="copyright">Copyright © 2016. Company Name. All Right Reserved</p>
      <ul class="social" aria-label="Social links">
        <li aria-label="Social link 1"></li>
        <li aria-label="Social link 2"></li>
        <li aria-label="Social link 3"></li>
        <li aria-label="Social link 4"></li>
        <li aria-label="Social link 5"></li>
      </ul>
    </footer>
  </main>
</body>
</html>
```